brightwell - Property Management DL Card

I am after a savvy designer to cut through junk mail! so many real estate agents use flyers to promote themselves and their business and usually sales. We are a property management firm (residential) and we want to represent landlords that have existing investment properties and need a quality agent to represent them. Can you help?
DL size, will be printed and delivered to mailboxes. For a look at our website go to www.brightwellrs.com.au. Keep it simple and clutter free.
it is to be double sided - with one side to be simple and clear - just our website, logo and telephone number on the back.
attached is our logo and our telephone number is 1300 48 92 16
the above are 2 essential elements to be included + our email address: admin@brightwellrs.com.au
also attached are our transparent price list

Target Market(s)
property investors,
people that manage properties themselves
Industry/Entity Type
Property Management
- arial
Look and feel

```html
<!DOCTYPE html>
<html lang="en">
<head>
<meta charset="utf-8">
<title>brightwell – Property Management DL Card</title>
<link rel="stylesheet" href="https://fonts.googleapis.com/css2?family=Open+Sans:wght@400;600&display=swap">
<style>
  :root {
    --page-bg: #e4e4e4;
    --card-stone: #b3ab9a;
    --card-frame: #c6c0b4;
    --panel-white: #ffffff;
    --ink-dark: #2b2b2b;
    --ink-contact: #3a3a3a;
    --bullet-grey: #9a9a9a;
    --banner-dark: #1c1c1c;
    --rule: #6e6658;
  }
  * { margin: 0; padding: 0; box-sizing: border-box; }
  html, body {
    width: 1200px; height: 1200px; overflow: hidden;
    background: var(--page-bg);
    font-family: "Open Sans", Arial, sans-serif;
  }
  .canvas { position: relative; width: 1200px; height: 1200px; }

  /* Front side */
  .card-front {
    position: absolute; left: 119px; top: 55px; width: 1002px; height: 500px;
    background: var(--card-frame);
  }
  .interior-photo {
    position: absolute; left: 0; top: 0; width: 669px; height: 500px;
    background: linear-gradient(120deg, #8a7d6c 0%, #b8ab98 30%, #d9d3c8 55%, #8c6a4c 80%, #5e4a38 100%);
  }
  .photo-inset {
    position: absolute; left: 22px; top: 23px; width: 647px; height: 454px;
    border: 0; background: rgba(255,255,255,0.08);
    box-shadow: 0 0 0 22px rgba(255,255,255,0.18);
  }
  .info-panel {
    position: absolute; left: 669px; top: 23px; width: 310px; height: 454px;
    background: var(--panel-white);
  }
  .tagline-banner {
    position: absolute; left: 521px; top: 117px; width: 442px; height: 27px;
    background: linear-gradient(90deg, rgba(28,28,28,0) 0%, var(--banner-dark) 6%, var(--banner-dark) 70%, rgba(28,28,28,0) 100%);
    color: #f2f2f2; font-size: 18px; font-weight: 600; line-height: 27px;
    padding-left: 13px;
  }
  .benefit-list {
    position: absolute; left: 699px; top: 155px; list-style: none;
    color: var(--ink-dark); font-size: 17px; line-height: 21.7px;
  }
  .benefit-list li { position: relative; padding-left: 15px; }
  .benefit-list li::before {
    content: ""; position: absolute; left: 1px; top: 7px; width: 7px; height: 7px;
    background: var(--bullet-grey); transform: rotate(45deg);
  }
  .brand-name-front {
    position: absolute; left: 669px; top: 388px; width: 310px; text-align: center;
    font-size: 40px; font-weight: 400; color: var(--ink-dark); letter-spacing: -0.5px;
  }

  /* Back side */
  .card-back {
    position: absolute; left: 119px; top: 637px; width: 1002px; height: 500px;
    background: var(--card-stone);
  }
  .brand-bar {
    position: absolute; left: 31px; top: 51px; width: 370px; height: 70px;
    background: linear-gradient(90deg, rgba(20,20,20,0) 0%, #141414 22%, #141414 62%, rgba(20,20,20,0) 100%);
  }
  .brand-name-back {
    position: absolute; left: 31px; top: 51px; width: 360px; text-align: center;
    font-size: 36px; font-weight: 400; line-height: 70px; color: #f2f2f2;
  }
  .contact-block {
    position: absolute; left: 555px; top: 380px;
    border-left: 2px solid var(--rule); padding-left: 19px;
    color: var(--ink-contact); font-size: 18px; line-height: 24px; letter-spacing: 0.3px;
  }
</style>
</head>
<body>
<div class="canvas">
  <section class="card-front">
    <div class="interior-photo" role="img" aria-label="Photograph of a furnished modern living and dining room"></div>
    <div class="photo-inset" aria-hidden="true"></div>
    <div class="info-panel"></div>
    <div class="tagline-banner">Property Management specialists</div>
    <ul class="benefit-list">
      <li>Excellent communication</li>
      <li>No hidden extras</li>
      <li>Minimal vacancy</li>
      <li>The best rent return</li>
    </ul>
    <div class="brand-name-front">brightwell</div>
  </section>

  <section class="card-back">
    <div class="brand-bar" aria-hidden="true"></div>
    <div class="brand-name-back">brightwell</div>
    <address class="contact-block" style="font-style:normal">
      1300 48 92 16<br>
      PO Box B527, Sydney North NSW, 2060<br>
      admin@brightwellrs.com.au
    </address>
  </section>
</div>
</body>
</html>
```